Polished Comb salon has created a lotion and needs help titling.Tides by polished comb ?Polis

The product is for a lotion bottle , my prototype lotion bottle size is an 8oz black lotion bottle with pump. I want the label in florescent green. It should tap into the emotion of potential buyers. The design should say choose me 😀(not literally ). Though the text should be clear and punchy . I.e " the skin multi-vitamin." I'm looking for a designer intrigued by the thought of my lotion. The label should be georgeous,informative, with visuals that immediately convey what my product is and how it works.Not distracting, but clear and punchy, with no expectation of someone to read more than a couple of words.The text should support the visual in a way the visual could not. It seems that nowadays visuals are taking over with very little text. The font,color , or punch of color should be enticing.
So here are some particular ideas of points about the lotion that could possibly be put on back as is done by lotion makers.
.ingredients
.TSA approved
.portion of proceeds go to lunch for little ones
.TC circled ( which is for pending trademark)
. I would like the word New in fluorescent on the bottle
.P.O Box address of place of manufacturing product.
. To help skin stay slightly moist,soft,and flexible with a smooth fine grained texture.

Target Market(s)

its a lotion so I want it available for all

Industry/Entity Type

Barber

Colors
9bcb3c

Requirements
Must have
• the word" Tides" and By polished comb...the word new on the bottle visible

```html
<!DOCTYPE html>
<html lang="en">
<head>
<meta charset="utf-8">
<title>Tides by Polished Comb – Multi-Vitamin Lotion Label</title>
<link rel="stylesheet" href="https://fonts.googleapis.com/css2?family=Montserrat:wght@600;700;800&display=swap">
<style>
  :root {
    --bg: #e9eaec;
    --ink: #111214;
    --label-black: #16171a;
    --lime: #9bcb3c;
    --lime-bright: #b6e04a;
    --lime-pale: #c9e87f;
    --lime-deep: #5f8a1a;
    --white: #ffffff;
  }
  * { box-sizing: border-box; margin: 0; padding: 0; }
  html, body { width: 1200px; height: 857px; overflow: hidden; }
  body {
    background: var(--bg);
    font-family: "Montserrat", Arial, sans-serif;
    color: var(--ink);
    position: relative;
  }
  .label {
    position: absolute;
    top: 110px;
    width: 500px;
    height: 640px;
    background: var(--label-black);
    border-radius: 14px;
    overflow: hidden;
  }
  .label--back { left: 60px; }
  .label--front { left: 640px; }

  .wave { position: absolute; left: 0; width: 100%; }

  .badge-new {
    position: absolute;
    border-radius: 50%;
    background: var(--lime-bright);
    color: var(--ink);
    font-weight: 800;
    display: flex; align-items: center; justify-content: center;
  }

  .brand { position: absolute; left: 0; right: 0; text-align: center; }
  .brand__name {
    display: block;
    color: var(--white);
    font-weight: 700;
    line-height: 1;
  }
  .brand__by {
    display: block;
    color: var(--lime);
    font-weight: 800;
    text-transform: uppercase;
    letter-spacing: 0.5px;
  }

  /* front */
  .label--front .badge-new { right: 26px; top: 24px; width: 66px; height: 66px; font-size: 16px; }
  .label--front .brand { top: 112px; }
  .label--front .brand__name { font-size: 104px; }
  .label--front .brand__by { font-size: 19px; margin-top: 10px; }

  .pill {
    position: absolute;
    left: 50%; transform: translateX(-50%);
    top: 300px;
    background: var(--lime-bright);
    border: 3px solid var(--ink);
    border-radius: 10px;
    padding: 7px 20px;
    font-weight: 800;
    font-size: 17px;
    white-space: nowrap;
  }
  .tagline-es {
    position: absolute;
    top: 352px; left: 70px; right: 70px;
    text-align: center;
    font-weight: 700;
    font-size: 14px;
    line-height: 1.35;
  }
  .claim {
    position: absolute;
    top: 478px; left: 0; right: 0;
    text-align: center;
    font-weight: 800;
    font-size: 21px;
    line-height: 1.35;
    text-transform: uppercase;
  }
  .net-weight {
    position: absolute;
    top: 548px; left: 0; right: 0;
    text-align: center;
    font-weight: 700;
    font-size: 20px;
  }

  /* back */
  .label--back .badge-new { right: 22px; top: 20px; width: 48px; height: 48px; font-size: 12px; }
  .label--back .brand { top: 34px; }
  .label--back .brand__name { font-size: 60px; }
  .label--back .brand__by { font-size: 12px; margin-top: 6px; }

  .intro {
    position: absolute;
    top: 140px; left: 20px; right: 20px;
    background: var(--lime);
    border-radius: 8px;
    padding: 10px 16px;
    color: var(--white);
    font-weight: 600;
    font-size: 12.5px;
    line-height: 1.4;
    text-align: center;
  }
  .about {
    position: absolute;
    top: 222px; left: 20px; width: 235px;
    color: var(--white);
    font-weight: 600;
    font-size: 12px;
    line-height: 1.45;
    text-align: justify;
  }
  .side { position: absolute; top: 222px; left: 268px; width: 212px; display: flex; flex-direction: column; gap: 8px; }
  .proceeds {
    background: var(--ink);
    border: 2px solid var(--lime);
    border-radius: 7px;
    color: var(--lime);
    font-weight: 800;
    font-size: 11.5px;
    text-align: center;
    padding: 6px 4px;
    line-height: 1.3;
  }
  .info-box {
    border-radius: 7px;
    padding: 8px 10px;
    color: var(--white);
    font-weight: 600;
    font-size: 11.5px;
    line-height: 1.45;
  }
  .info-box--ingredients { background: var(--lime); }
  .info-box h3 { font-size: 12px; font-weight: 800; margin-bottom: 3px; }
  .info-box--directions { background: var(--white); color: var(--lime-deep); font-weight: 700; }

  .contact {
    position: absolute;
    left: 268px; top: 556px; width: 220px;
    font-size: 10.5px;
    font-weight: 600;
    line-height: 1.4;
  }
  .contact strong { font-weight: 800; }
</style>
</head>
<body>

<section class="label label--back" aria-label="Back label">
  <svg class="wave" style="top:250px;height:390px" viewBox="0 0 500 390" preserveAspectRatio="none" aria-hidden="true">
    <defs>
      <linearGradient id="backGreen" x1="0" y1="0" x2="0" y2="1">
        <stop offset="0" stop-color="#a6d443"/>
        <stop offset="1" stop-color="#87b92e"/>
      </linearGradient>
    </defs>
    <path d="M0 40 C120 0 200 60 320 30 C400 10 460 20 500 30 L500 390 L0 390 Z" fill="url(#backGreen)"/>
    <path d="M0 90 C140 50 260 110 500 60 L500 390 L0 390 Z" fill="#9bcb3c" opacity="0.6"/>
  </svg>

  <div class="badge-new">NEW</div>
  <div class="brand">
    <span class="brand__name">Tides</span>
    <span class="brand__by">By Polished Comb</span>
  </div>

  <p class="intro">Tides multi-vitamin lotion, supplies the skin with the nutrients needed for daily skin health. With vitamins (A,C,D,E) that repair, replenish, and promote general skin health.</p>

  <p class="about">Dermatologist describe healthy skin as slightly moist, soft, and flexible and its texture is smooth and fine grained. Tides lotion is designed with this goal in mind. That is because at "Tides" we know the importance of healthy skin. Our skin is our first line of defense against bacteria, minor injuries, chemical substances and temperature. With this in mind, we at Tides by polished comb have engineered this product.</p>

  <div class="side">
    <p class="proceeds">PORTION OF PROCEEDS<br>GO TO LUNCH FOR LITTLE ONES</p>
    <div class="info-box info-box--ingredients">
      <h3>INGREDIENTS:</h3>
      <p>Distilled Water (H2O), Grapeseed oil, Coconut oil, Jo joba oil, Beeswax, Vita-A, Vita-C, Vita-D, Vita-E, Aloe Vera, Potassium sorbate, Honey, Glycerin, Stearic acid, Citric acid.</p>
    </div>
    <p class="info-box info-box--directions">Directions: For best results apply daily as needed to clean skin.</p>
  </div>

  <p class="contact">
    <strong>QUESTIONS OR CONCERNS:</strong><br>
    hello@polishedcombsalon.example<br>
    P.O. Box 4410<br>
    Harbor City ca 90710<br>
    (555)014-2287 (555)019-6631
  </p>
</section>

<section class="label label--front" aria-label="Front label">
  <svg class="wave" style="top:270px;height:370px" viewBox="0 0 500 370" preserveAspectRatio="none" aria-hidden="true">
    <defs>
      <linearGradient id="frontGreen" x1="0" y1="0" x2="0" y2="1">
        <stop offset="0" stop-color="#b6e04a"/>
        <stop offset="0.55" stop-color="#9bcb3c"/>
        <stop offset="1" stop-color="#a9d64a"/>
      </linearGradient>
    </defs>
    <path d="M0 70 C110 20 220 40 300 30 C400 15 460 0 500 10 L500 310 L0 310 Z" fill="url(#frontGreen)"/>
    <path d="M0 150 C150 100 300 170 500 110 L500 310 L0 310 Z" fill="#c9e87f" opacity="0.45"/>
  </svg>

  <div class="badge-new">NEW</div>
  <div class="brand">
    <span class="brand__name">Tides</span>
    <span class="brand__by">By Polished Comb</span>
  </div>

  <p class="pill">THE SKIN MULTI-VITAMIN LOTION</p>
  <p class="tagline-es">Tides de Polished Comb, la piel multi vitaminas loción, mantiene la piel suave, lisa y ligeramente húmeda</p>

  <p class="claim">Keeps skin soft,<br>smooth and slightly moist</p>
  <p class="net-weight">Net Weight: 8oz</p>
</section>

</body>
</html>
```